Paint Retail Store needs a logo/label redesign.

We are redesigning a label for one of our products. We are a paint retail store that specializes on selling premium paint at outlet prices called Coat & Gleam. We want the redesign to exude professionalism and cleanliness. Attached is a picture of our current label. We want the logo Coat & Gleam to be modified to a more modern feel that still incorporates the iconic paint roller element that has been part of our brand identity. We want the description of: Exceptional Durability/ Luxurious Finish to be included in the front of the label to attract our clients. Include all of the information and description of the current label to the new label. Attached are pictures of our competitors labels so you have an idea of what we are looking for. We also want the background of the label to be a clean solid color.

Target Market(s)

Home Owners, DIY enthusiasts, Contractors/painters, interior designers

Industry/Entity Type

Paint and Coatings retail store

Colors

Designer to choose colors to be used in the design.

Requirements
Must have
• Semigloss Finish, Exceptional Durability, Luxurios Finish. Include all the information that are on the side of the current label to the new label. Include the phrase: Made in the US.
Nice to have
• A redesign of the logo: Coat & Gleam to convey a more modern/professional look.
Should not have
• Feminine colors.

```html
<!DOCTYPE html>
<html lang="en">
<head>
<meta charset="utf-8">
<title>Coat &amp; Gleam Semi-Gloss Label</title>
<link href="https://fonts.googleapis.com/css2?family=Montserrat:wght@400;500;600;700;800;900&display=swap" rel="stylesheet">
<style>
  :root{
    --stage:#ececec;
    --orange-deep:#e4570c;
    --orange-mid:#f07a14;
    --orange-light:#f89a2a;
    --gold:#fbb73a;
    --rust:#c94d0c;
    --ink:#111111;
    --white:#ffffff;
    --body:'Montserrat', Arial, sans-serif;
  }
  *{margin:0;padding:0;box-sizing:border-box}
  html,body{width:878px;height:1200px;overflow:hidden;background:var(--stage)}
  body{font-family:var(--body);color:var(--white)}
  .label{position:absolute;left:0;top:280px;width:878px;height:640px;overflow:hidden;
    background:linear-gradient(160deg,var(--orange-light) 0%,var(--orange-mid) 35%,var(--orange-deep) 100%)}
  .side{position:absolute;top:0;height:640px;font-weight:400}
  .side b{font-weight:700}
  .left{left:29px;width:244px;font-size:8.2px;line-height:11.4px;letter-spacing:-0.1px}
  .block{position:absolute;left:0;width:100%}
  .prep-title{font-size:11px;line-height:12px;font-weight:600;letter-spacing:.1px}
  .ingredients{position:absolute;left:84px;top:538px;width:111px;height:92px;background:var(--white);
    border:1px solid var(--ink);border-radius:4px;color:var(--ink);font-size:6.4px;line-height:7.7px;padding:4px 6px}
  .ingredients .head{display:flex;justify-content:space-between;font-weight:500;margin-bottom:2px}
  .ingredients .row{display:flex;justify-content:space-between}
  .ingredients .foot{text-align:center;font-weight:700;margin-top:3px;line-height:7px}
  .volume{position:absolute;left:222px;top:588px;width:104px;text-align:center;font-size:10.5px;line-height:13px;font-weight:500}
  .origin{position:absolute;left:222px;top:620px;width:104px;text-align:center;font-size:7.5px;line-height:9px;font-weight:700;letter-spacing:.4px}
  .front{position:absolute;left:281px;top:0;width:341px;height:326px;background:var(--white);border-radius:0 0 48px 48px}
  .brand{position:absolute;left:18px;top:62px;width:310px;color:var(--ink);font-weight:900;font-size:70px;line-height:66px;letter-spacing:-2px}
  .brand-dot{position:absolute;right:26px;top:78px;width:26px;height:26px;border-radius:50%;background:var(--orange-mid)}
  .tagline{position:absolute;left:0;top:268px;width:100%;text-align:center;color:var(--ink);font-size:16px;line-height:19px;font-weight:400}
  .finish{position:absolute;left:281px;top:340px;width:341px;text-align:center;font-size:46px;line-height:52px;font-weight:900;letter-spacing:-1px}
  .latex-banner{position:absolute;left:324px;top:413px;width:247px;height:138px}
  .benefit{position:absolute;left:281px;top:560px;width:341px;text-align:center;color:var(--gold);font-size:14px;line-height:16px;font-weight:800}
  .freeze-tab{position:absolute;left:332px;top:603px;width:237px;height:45px;background:var(--white);border-radius:26px 26px 0 0;
    display:flex;align-items:center;justify-content:center;gap:12px;color:var(--rust)}
  .freeze-tab span{font-size:14px;line-height:12px;font-weight:800;text-align:center;padding-bottom:6px}
  .freeze-tab svg{margin-bottom:6px}
  .right{left:645px;width:230px}
  .notice{position:absolute;left:0;width:100%;text-align:center;font-weight:800;font-size:14px;line-height:19px}
  .cleanup{position:absolute;left:0;top:73px;width:100%;text-align:center;font-size:10.5px;line-height:13.5px}
  .steps{position:absolute;left:41px;top:166px;display:grid;grid-template-columns:repeat(3,39px);column-gap:12px;row-gap:9px}
  .step .pict{width:39px;height:38px;background:var(--ink);border:1.5px solid var(--white)}
  .step p{font-size:4.6px;line-height:5.6px;margin-top:2px}
  .safety{position:absolute;left:0;width:100%;font-size:7.5px;line-height:11px;letter-spacing:-0.15px}
  .safety b{font-weight:700}
</style>
</head>
<body>
<main class="label">

  <section class="side left">
    <p class="block" style="top:29px"><b>Where To Use:</b> Walls, cabinets, ceilings, trim and doors. Use over drywall, wood, concrete/brick, plaster and wallpaper. See bellow for preparation steps.</p>
    <p class="block" style="top:85px"><b>How Much You Need:</b> For one coat coverage, apply at a maximum of 400 square feet per gallon. Rough or textured urfaces may require more-allow for 125-300 square feet per gallon. Do not thin.</p>
    <p class="block" style="top:154px"><b>What Tools To Use:</b> May be applied with a quality roller, a nylon/polyester brush, or a paint pad.</p>
    <p class="block" style="top:188px"><b>How To Apply:</b> Room and surface temperature must be 50 degrees Fahrenheit. Allow at least 4 hours of drying time before recoating. Mix gallons togheter for color and sheen uniformity when using more than one gallon of the same product.</p>
    <p class="block" style="top:258px">Care for Freshly Painted Surfaces; Freshly painted surfaced may be washed either 30 days-Until then avoid touching, wiping, or wetting the surface. Then clean with mild, non-abrasive, non-oily cleanser and water. Do not place objects on painted sirfaces untill throughly dry. Soap and Water Cleanup</p>
    <h3 class="block prep-title" style="top:337px">HOW TO PREPARE THE SURFACE</h3>
    <p class="block" style="top:356px"><b>Previously Painted Surfaces:</b> Remove loose paint, Wash with a mild, non-abrasive, non-oily cleanser and water. Rinse completely, let dry. Patch holes and cracks with speckling paste and let dry. Sand patched area and wipe off residue. Send all smooth or glossy surfaces, rinse well.</p>
    <p class="block" style="top:423px"><b>Unpainted Surfaces:</b> Wallboard or Drywall. Concrete/brick. Allow new masonry to sure at least 30 days. Etch smooth unpainted concrete. Remove all loose concrete and efflorescence. Rinse and allow to dry Plaster (new)-Must be dried and cured for 30 days. Prime with primer. Let dry 4 hours before top coating. Wallpaper Vinyl coated wallpaper may be coated if all seams and edges are glued tight. Self-sand and wipe clean. Use primer and alllow 24 hours to dry.</p>
  </section>

  <div class="ingredients">
    <div class="head"><span>CAS NO.</span><span>Ingredients</span></div>
    <div class="row"><span>7732-18-5</span><span>Water</span></div>
    <div class="row"><span>Propietary</span><span>Vinyl Polymer</span></div>
    <div class="row"><span>13463-67-7</span><span>Titanium Dioxide</span></div>
    <div class="row"><span>Propietary</span><span>Acrylic Polymer</span></div>
    <div class="row"><span>471-34-1</span><span>Calcium Carbonate</span></div>
    <div class="row"><span>14464-46-1</span><span>Cristobalite</span></div>
    <div class="foot">NON-PHOTOCHEMICALLY<br>REACTIVE</div>
  </div>

  <p class="volume">1 Gal.<br>(124 OZ/3.667 Lts.)</p>
  <p class="origin">MADE IN THE US</p>

  <section class="front">
    <h1 class="brand">Coat &amp;<br>Gleam</h1>
    <div class="brand-dot"></div>
    <p class="tagline">PREMIUM PAINT AT OUTLET<br>PRICES SEMI-GLOSS</p>
  </section>

  <h2 class="finish">SEMI-GLOSS</h2>

  <svg class="latex-banner" role="img" aria-label="Latex paint banner with paint roller illustration" viewBox="0 0 247 138">
    <defs>
      <linearGradient id="bannerTone" x1="0" y1="0" x2="1" y2="1">
        <stop offset="0" stop-color="#fbc25a"/>
        <stop offset="1" stop-color="#f29a22"/>
      </linearGradient>
    </defs>
    <rect x="0" y="0" width="247" height="138" rx="10" fill="url(#bannerTone)"/>
  </svg>

  <p class="benefit">EXCEPTIONAL DURABILITY &amp;<br>LUXURIOUS FINISH</p>

  <div class="freeze-tab">
    <svg width="16" height="16" viewBox="0 0 16 16" stroke="currentColor" stroke-width="2" stroke-linecap="round"><path d="M8 1v14M2 4.5l12 7M2 11.5l12-7"/></svg>
    <span>PROTECT FROM<br>FREEZING</span>
    <svg width="16" height="16" viewBox="0 0 16 16" stroke="currentColor" stroke-width="2" stroke-linecap="round"><path d="M8 1v14M2 4.5l12 7M2 11.5l12-7"/></svg>
  </div>

  <section class="side right">
    <h3 class="notice" style="top:27px">SOLID VINYL WALLPAPER<br>CANNOT BE PAINTED.</h3>
    <p class="cleanup">Cleanup: Clean tools, spills and splatters immediately with soap and water</p>
    <h3 class="notice" style="top:116px">KEEP FROM FREEZING-DO<br>NOT THIN</h3>
    <div class="steps">
      <div class="step"><div class="pict" role="img" aria-label="Pictogram: clean surface"></div><p>Clean, dull and dry surface</p></div>
      <div class="step"><div class="pict" role="img" aria-label="Pictogram: stir paint"></div><p>Stir paint thoroughly</p></div>
      <div class="step"><div class="pict" role="img" aria-label="Pictogram: start at ceiling"></div><p>Start at ceiling edge</p></div>
      <div class="step"><div class="pict" role="img" aria-label="Pictogram: roller pattern"></div><p>Paint "N" pattern - still in</p></div>
      <div class="step"><div class="pict" role="img" aria-label="Pictogram: paint trim"></div><p>Paint trim last</p></div>
      <div class="step"><div class="pict" role="img" aria-label="Pictogram: soap and water cleanup"></div><p>Soap and water clean up</p></div>
    </div>
    <p class="safety" style="top:294px"><b>CAUTIONS CONTAINS CRYSTALLINE SILICA-</b> Use only with adecuate ventilation. To avoid overexposure, open windows and doors or use other means to ensure fresh air entry during plication and drying. If you experience eye watering, headaches, or dizzyness, increase fresh air, or wear respiratory protection or leavethe area. Adecuate ventilation required when sending or abrading the dried film. If adequate ventilation cannot ve provided wear an approved particulate respirator. Follow resporator manufacturer's directions for respirator use. Avoid contact with eyes and skin. Wash hands after using. Keep container closed when not in use. Do not transfer contents to other containers for storage</p>
    <p class="safety" style="top:455px"><b>FIRST AID:</b> In case of eye contact, flush thoroughly with large amounts of water. Get medical attention if tirritation persists. If allowed, call Poison Control Center, hospital emergency room, or phisician Inmediately.</p>
    <p class="safety" style="top:510px"><b>DELAYED EFFECTS FROM LONG TERM OVEREXPOSURE.</b> Abrading or sanding of the dry film may release crystaline silica which has been shown to cause lung damage and cancer under long term exposure.</p>
    <p class="safety" style="top:566px"><b>WARNING:</b> This product contains chemicals known to the State of California to cause cancer and birth defects or other reproductive harm.</p>
    <p class="safety" style="top:609px"><b>DO NOT TAKE INTERNALLY<br>KEEP OUT OF THE REACH OF CHILDREN.</b></p>
  </section>

</main>
</body>
</html>
```